CalmPeak Nurses' Manifesto

Design a manifesto to inspire and motivate nurses to work at minimum standards of excellence in their nursing practice.

The manifesto will become a feature of our website, at conferences, workshops and retreats. It will also be featured on other marketing tools.

Primary Market:
Nurses and/or other healthcare professionals (specifically Doctors, Occupational Therapists, Psychologists and Social Workers).

However the manifesto is equally applicable to all nurses and healthcare professionals from new graduates to very experienced senior clinicians, administration officers,managers and healthcare executive personnel.

Mainly females and primarily 35 to 65 years old, which suggests people in this target age group have extensive experience, but have become jaded'.

The purpose of our business is to assist healthcare professionals, primarily nurses, to maintain their enthusiasm and excellence in service provision, for their benefit as well as the benefit of the clients.

I have attached:
File 1: Copy Samples and examples: which has the copy for the manifesto, examples that appeal to us and our 3 attempts.
File 2: Our colour Spec Sheet, HOWEVER the colours are not necessary limited to these colours. These colours are not in the logo that will be on the manifesto. The colours on the logo attached can/or also be used.
File 3: Prototype logo. The final logo will be available within 3 to 4 days.

Industry/Entity Type

Healthcare

Requirements
Must have
• Must use the copy as per the attached file.

It should be contemporary, eye catching and motivational.

Should not have
• MUST BE EASY TO READ. Each line MUST be clearly defined from each other.

```html
<!DOCTYPE html>
<html lang="en">
<head>
<meta charset="utf-8">
<title>CalmPeak Nurses' Manifesto</title>
<link rel="stylesheet" href="https://fonts.googleapis.com/css2?family=Source+Sans+3:wght@400;600;700&display=swap">
<style>
:root{
  --sky:#4db3e8;
  --blue:#2f7bd6;
  --navy:#1f3a93;
  --deep-blue:#2e6fb5;
  --pale-blue:#9ccbee;
  --magenta:#e62ea0;
  --green:#3a9a2a;
  --lime:#7ac943;
  --leaf:#6cc630;
  --red:#e8231e;
  --orange:#f26722;
  --purple:#7a4bd6;
  --brown:#a0571c;
  --ink:#111;
  --band:#5b8fd6;
  --paper:#fff;
}
*{margin:0;padding:0;box-sizing:border-box}
html,body{width:900px;height:1200px;overflow:hidden;background:var(--paper)}
.manifesto{position:relative;width:900px;height:1200px;overflow:hidden;
  font-family:"Source Sans 3","Myriad Pro",sans-serif;font-weight:400}
.line{position:absolute;white-space:nowrap;line-height:1;letter-spacing:0.04em;text-align:justify;text-align-last:justify}
.free{position:absolute;white-space:nowrap;line-height:1}
.tracked{letter-spacing:0.04em}
.vertical{position:absolute;white-space:nowrap;line-height:1;transform-origin:top left;transform:rotate(-90deg)}
.top-band{position:absolute;left:22px;top:0;width:856px;height:14px;background:var(--band)}
.foot-mark{position:absolute;left:40px;top:1138px;width:14px;height:36px;background:var(--band)}
.dream-band{position:absolute;left:490px;top:1125px;width:388px;height:50px;background:var(--band);
  color:var(--paper);font-size:27px;line-height:50px;padding-left:26px}
.dream-band b{font-size:38px;font-weight:400}
.brand{position:absolute;left:66px;top:1134px;display:flex;align-items:center;gap:10px;
  color:var(--deep-blue);font-size:26px;line-height:1}
.brand i{display:block;width:20px;height:20px;border-radius:50%;background:var(--deep-blue)}
.portrait{position:absolute;left:695px;top:818px;width:185px;height:307px;
  background:linear-gradient(180deg,#e9d8cc 0%,#cfe9ee 30%,#8fd3da 60%,#6ec3cc 100%);border-radius:90px 90px 0 0}
.sky{color:var(--sky)} .blue{color:var(--blue)} .navy{color:var(--navy)} .deep{color:var(--deep-blue)}
.pale{color:var(--pale-blue)} .magenta{color:var(--magenta)} .green{color:var(--green)} .lime{color:var(--lime)}
.leaf{color:var(--leaf)} .red{color:var(--red)} .orange{color:var(--orange)} .purple{color:var(--purple)}
.brown{color:var(--brown)} .ink{color:var(--ink)}
.bold{font-weight:700}
</style>
</head>
<body>
<main class="manifesto">
  <div class="top-band"></div>

  <!-- Opening -->
  <div class="free sky" style="left:40px;top:20px;font-size:80px">Nurse</div>
  <div class="line deep" style="left:244px;top:19px;width:366px;font-size:30px"><span>Deliver</span> <span style="font-size:58px">care</span> <span>skillfully.</span></div>
  <div class="line sky" style="left:40px;top:95px;width:192px;font-size:38px">with open</div>
  <div class="free magenta tracked" style="left:243px;top:82px;font-size:60px">Learn</div>
  <div class="line magenta" style="left:407px;top:79px;width:203px;font-size:26px">s o m e t h i n g</div>
  <div class="line magenta" style="left:407px;top:106px;width:203px;font-size:27px">new each day.</div>
  <div class="line sky" style="left:40px;top:132px;width:470px;font-size:39px">hands, hearts and minds.</div>

  <div class="free green tracked" style="left:628px;top:16px;font-size:98px">Trust</div>
  <div class="line green" style="left:628px;top:111px;width:230px;font-size:21px">your knowledge and</div>
  <div class="line green" style="left:628px;top:135px;width:230px;font-size:21px">seek advice only from</div>
  <div class="line green" style="left:628px;top:153px;width:230px;font-size:21px"><span>respected</span> <span style="font-size:27px">sources.</span></div>

  <!-- Column one -->
  <div class="line ink" style="left:40px;top:170px;width:348px;font-size:28px"><span>Look after</span> <span style="font-size:50px">yourself</span></div>
  <div class="line ink" style="left:40px;top:212px;width:348px;font-size:28px"><span>and value your</span> <span style="font-size:42px">health</span></div>
  <div class="line ink" style="left:40px;top:257px;width:348px;font-size:28px">as much as you value</div>
  <div class="line ink" style="left:40px;top:290px;width:348px;font-size:28px">the health of others.</div>
  <div class="line magenta" style="left:38px;top:322px;width:348px;font-size:29px"><span style="font-size:46px">Be</span> a lifelong learner.</div>
  <div class="line ink" style="left:38px;top:366px;width:345px;font-size:22px"><span style="font-size:60px">Respect</span> the limits of</div>
  <div class="line ink" style="left:38px;top:427px;width:345px;font-size:22px"><span style="font-size:28px">people</span>’s knowledge and share</div>
  <div class="line ink" style="left:38px;top:458px;width:345px;font-size:21px">your knowledge generously.</div>
  <div class="line navy" style="left:38px;top:490px;width:345px;font-size:31px"><span style="font-size:62px">Smile</span> and infect</div>
  <div class="line navy" style="left:38px;top:545px;width:345px;font-size:31px">others with your</div>
  <div class="line navy" style="left:38px;top:576px;width:345px;font-size:29px">h a p p i n e s s</div>
  <div class="line lime" style="left:38px;top:616px;width:345px;font-size:50px"><span class="bold" style="font-size:52px">Seek</span> success</div>
  <div class="free lime tracked" style="left:38px;top:666px;font-size:40px">firstly from within.</div>
  <div class="vertical pale" style="left:38px;top:824px;font-size:42px">Adopt</div>
  <div class="line pale" style="left:90px;top:720px;width:288px;font-size:30px">a ‘can do’ attitude</div>
  <div class="line pale" style="left:90px;top:755px;width:288px;font-size:30px">to everything that</div>
  <div class="line pale" style="left:90px;top:789px;width:288px;font-size:30px">comes your way.</div>

  <!-- Column two -->
  <div class="free blue tracked" style="left:400px;top:178px;font-size:66px">Respond</div>
  <div class="line blue" style="left:400px;top:251px;width:264px;font-size:23px">to complex situations</div>
  <div class="line blue" style="left:400px;top:275px;width:264px;font-size:44px">innovatively,</div>
  <div class="line blue" style="left:400px;top:313px;width:264px;font-size:23px"><span style="font-size:40px">creatively</span> and</div>
  <div class="line blue" style="left:400px;top:362px;width:264px;font-size:23px"><span style="font-size:37px">safely</span> within the</div>
  <div class="line blue" style="left:400px;top:402px;width:264px;font-size:23px">scope of your</div>
  <div class="line blue" style="left:400px;top:434px;width:264px;font-size:23px">p r a c t i c e .</div>
  <div class="line red" style="left:398px;top:466px;width:266px;font-size:62px">Support</div>
  <div class="line red" style="left:398px;top:538px;width:266px;font-size:33px">your colleagues</div>
  <div class="line red" style="left:398px;top:575px;width:266px;font-size:33px">and champion</div>
  <div class="line red" style="left:398px;top:613px;width:266px;font-size:33px">their purpose.</div>
  <div class="vertical purple" style="left:403px;top:828px;font-size:56px">Always</div>
  <div class="line purple" style="left:467px;top:670px;width:196px;font-size:31px">be solution</div>
  <div class="line purple" style="left:467px;top:703px;width:190px;font-size:31px">f o c u s e d .</div>
  <div class="line purple" style="left:467px;top:750px;width:388px;font-size:31px">do the right thing</div>
  <div class="line purple" style="left:467px;top:790px;width:388px;font-size:31px">without exception.</div>

  <!-- Column three -->
  <div class="line ink" style="left:678px;top:182px;width:180px;font-size:46px">Choose</div>
  <div class="line ink" style="left:678px;top:228px;width:180px;font-size:23px">t h o u g h t s</div>
  <div class="line ink" style="left:678px;top:253px;width:180px;font-size:25px">wisely, they</div>
  <div class="line ink" style="left:678px;top:280px;width:180px;font-size:25px">create your</div>
  <div class="free ink" style="left:678px;top:306px;font-size:42px;letter-spacing:0.09em">reality.</div>
  <div class="line orange" style="left:678px;top:362px;width:180px;font-size:34px">Celebrate,</div>
  <div class="line orange" style="left:678px;top:398px;width:180px;font-size:23px"><span style="font-size:34px">respect</span> and</div>
  <div class="line orange" style="left:678px;top:432px;width:180px;font-size:36px">v a l u e</div>
  <div class="line orange" style="left:678px;top:470px;width:180px;font-size:27px">the diversity</div>
  <div class="line orange" style="left:678px;top:498px;width:180px;font-size:27px">of Australian</div>
  <div class="line orange" style="left:678px;top:527px;width:180px;font-size:23px">c u l t u r e .</div>
  <div class="line leaf" style="left:678px;top:555px;width:180px;font-size:27px"><span style="font-size:60px">You</span> are</div>
  <div class="free leaf" style="left:678px;top:617px;font-size:54px">unique,</div>
  <div class="line leaf" style="left:678px;top:673px;width:180px;font-size:27px">revel in your</div>
  <div class="line leaf" style="left:678px;top:706px;width:180px;font-size:27px">individuality.</div>

  <!-- Closing -->
  <div class="line deep" style="left:38px;top:826px;width:652px;font-size:31px"><span style="font-size:54px">Delight</span> <span>your</span> <span style="font-size:37px">clients</span> <span>and</span> <span style="font-size:39px">colleagues</span></div>
  <div class="free deep tracked" style="left:38px;top:878px;font-size:30px">by exceeding their expectations.</div>
  <div class="line red" style="left:40px;top:912px;width:515px;font-size:30px"><span>Only</span> <span style="font-size:40px">follow</span> <span>exceptional</span> <span style="font-size:40px">leaders.</span></div>
  <div class="free brown tracked" style="left:40px;top:953px;font-size:58px">Always</div>
  <div class="free brown tracked" style="left:40px;top:1015px;font-size:40px">lead with</div>
  <div class="free brown" style="left:40px;top:1055px;font-size:40px">purpose, passion</div>
  <div class="free brown" style="left:295px;top:1087px;font-size:40px">and commitment.</div>
  <div class="line sky" style="left:233px;top:971px;width:357px;font-size:35px">If there is no one left</div>
  <div class="free sky tracked" style="left:233px;top:1016px;font-size:35px">to follow, then</div>
  <div class="free sky" style="left:492px;top:1020px;font-size:58px">lead!</div>

  <div class="portrait" role="img" aria-label="Photo of a smiling nurse in teal scrubs holding a clipboard"></div>

  <div class="foot-mark"></div>
  <div class="brand"><i></i><span>CalmPeak</span></div>
  <div class="dream-band">Live your <b>dream.</b></div>
</main>
</body>
</html>
```